Ridgeline Haul Carriers - Website

A clean, not cluttered informative website for our business. We specialize in the transportation of radioactive materials across North America. The site is mostly for information about our company and will not be used to attract business but will be used to attract employee's mainly drivers. Driver's are very hard to find in our area. One of the pages needs to be a job's posting page with an apply now button. Either an application can be filled out there or a resume can be uploaded which ever functionality works better. I would like a website that I can easily edit, ability to change text and photos.

Number of Pages Required

5+ page

Colors

Designer to choose colors to be used in the design.

Requirements
Must have
• Home - About - Services - Jobs - Contact pages
• A way prospective employee's can apply or upload their resume to be emailed to me
• Very clean apperance
Should not have
• I don't want it to be busy

```html
<!DOCTYPE html>
<html lang="en">
<head>
<meta charset="utf-8">
<title>Ridgeline Haul Carriers</title>
<link href="https://fonts.googleapis.com/css2?family=Play:wght@400;700&family=Poppins:wght@400;500&display=swap" rel="stylesheet">
<style>
:root{
  --blue:#1a6db5;
  --blue-dark:#0f4f86;
  --grey-text:#6f7073;
  --ink:#222222;
  --body:#333333;
  --rule:#e6e6e6;
  --footer:#8b8b8f;
  --footer-line:#ffffff;
  --bar:#1b6cb5;
  --white:#ffffff;
}
*{margin:0;padding:0;box-sizing:border-box}
html,body{width:1200px;height:2410px;overflow:hidden;background:var(--white)}
body{position:relative;font-family:"Poppins",sans-serif;color:var(--body)}
.abs{position:absolute}
/* header */
.brand{left:80px;top:44px;font-family:"Play",sans-serif;font-weight:700;font-size:30px;color:var(--blue);letter-spacing:.5px}
.top-contact{top:20px;right:84px;display:flex;gap:26px;font-size:16px;color:var(--ink);align-items:center}
.top-contact span{display:flex;align-items:center;gap:10px}
.nav{top:74px;right:84px;display:flex;gap:48px;font-size:17px;color:var(--ink)}
.nav .active{color:var(--blue)}
/* hero */
.hero{left:0;top:128px;width:1200px;height:490px;background:linear-gradient(180deg,#c3c5c8 0%,#9a948c 30%,#6e6864 60%,#4f5257 100%)}
.hero-title{left:0;width:1308px;top:452px;text-align:center;font-family:"Poppins",sans-serif;font-weight:500;font-size:41px;line-height:50px;color:var(--white);text-shadow:0 2px 6px rgba(0,0,0,.55)}
.hero-arrow{top:343px;width:34px;height:34px;background:rgba(30,30,30,.55)}
/* sections */
.section-title{left:0;width:1200px;text-align:center;font-family:"Play",sans-serif;font-size:36px;color:var(--grey-text)}
.section-title b{color:var(--blue);font-weight:700}
.title-rule{height:2px;background:#9a9a9a}
.about-sub{top:755px;left:0;width:1200px;text-align:center;font-size:20px;color:var(--blue)}
.about-text{top:788px;left:98px;width:1004px;text-align:center;font-size:16px;line-height:29px;color:var(--ink)}
.btn{display:flex;align-items:center;justify-content:center;background:var(--blue);color:var(--white);font-size:19px;box-shadow:3px 4px 6px rgba(0,0,0,.35)}
.divider{left:104px;top:1041px;width:996px;height:1px;background:var(--rule)}
.card{top:1219px;width:241px}
.card .photo{width:241px;height:206px;border:2px solid var(--blue);padding:5px;background:#fff}
.card .photo div{width:100%;height:100%}
.card h3{margin-top:18px;text-align:center;font-family:"Play",sans-serif;font-weight:700;font-size:19px;color:var(--ink)}
.card p{margin-top:10px;text-align:center;font-size:14.5px;line-height:25.7px;color:var(--ink)}
.card .btn{width:136px;height:48px;margin:24px auto 0}
/* drivers band */
.band{left:0;top:1755px;width:1200px;height:289px;background:linear-gradient(180deg,#f3f6f8 0%,#dfe5ea 70%,#b9c0c6 100%)}
.band-photo{left:820px;top:1755px;width:380px;height:289px;background:linear-gradient(90deg,rgba(223,227,230,0) 0%,#c9cdd1 18%,#7e8287 55%,#2b2c2e 100%)}
.band-title{left:289px;top:1822px;font-family:"Play",sans-serif;font-size:36px;color:var(--grey-text)}
.band-title b{color:var(--blue);font-weight:700}
.band-text{left:289px;top:1876px;width:560px;font-size:16.5px;line-height:29px;color:var(--ink)}
.apply{left:299px;top:1938px;width:461px;height:61px;font-family:"Play",sans-serif;font-weight:700;font-size:21px;border:1px solid var(--blue-dark)}
/* footer */
.footer{left:0;top:2044px;width:1200px;height:317px;background:var(--footer)}
.f-head{top:2082px;font-family:"Play",sans-serif;font-weight:700;font-size:17px;color:var(--white)}
.f-line{top:2120px;width:48px;height:2px;background:var(--footer-line)}
.f-links{left:80px;top:2143px;list-style:none;font-size:15px;line-height:36px;color:var(--white)}
.f-contact{left:239px;font-size:15px;line-height:24px;color:var(--white);display:flex;gap:14px}
.map{left:570px;top:2146px;width:283px;height:168px;background:linear-gradient(135deg,#eef0ee,#dfe3df)}
.social-c{top:2147px;width:30px;height:30px;border-radius:50%;background:var(--blue)}
.f-apply{left:915px;top:2191px;width:203px;height:80px;font-family:"Play",sans-serif;font-weight:700;font-size:15px;line-height:19px;text-align:center;border:1px solid var(--blue-dark)}
.bar{left:0;top:2361px;width:1200px;height:49px;background:var(--bar)}
.copy{left:82px;top:2374px;font-size:14px;color:var(--white)}
.social-s{top:2370px;width:30px;height:30px}
</style>
</head>
<body>
<header>
  <div class="abs brand">Ridgeline Haul Carriers</div>
  <div class="abs top-contact">
    <span><svg width="30" height="20" viewBox="0 0 30 20"><rect x="1" y="1" width="28" height="18" fill="none" stroke="#1a6db5" stroke-width="2"/><path d="M1 1 L15 12 L29 1" fill="none" stroke="#1a6db5" stroke-width="2"/></svg>inquiry@ridgelinehaul.com</span>
    <span><svg width="24" height="24" viewBox="0 0 24 24"><path d="M6 2 L10 7 L8 10 Q10 14 14 16 L17 14 L22 18 L19 22 Q10 22 4 14 Q1 8 6 2Z" fill="#1a6db5"/></svg>555.014.2290</span>
  </div>
  <nav class="abs nav"><span class="active">Home</span><span>About Us</span><span>Services</span><span>Jobs</span><span>Contact Us</span></nav>
</header>

<section>
  <div class="abs hero" role="img" aria-label="Photo of a semi truck hauling radioactive material containers on a flatbed trailer beside a brick building"></div>
  <div class="abs hero-arrow" style="left:0"><svg width="34" height="34"><path d="M20 10 L13 17 L20 24" stroke="#fff" stroke-width="3" fill="none"/></svg></div>
  <div class="abs hero-arrow" style="right:0"><svg width="34" height="34"><path d="M14 10 L21 17 L14 24" stroke="#fff" stroke-width="3" fill="none"/></svg></div>
  <h1 class="abs hero-title">We Specialize In The<br>Transportation of Radioactive<br>Materials Across North America</h1>
</section>

<section>
  <h2 class="abs section-title" style="top:680px"><b>About Ridgeline Haul</b> Carriers</h2>
  <div class="abs title-rule" style="top:735px;left:520px;width:160px"></div>
  <p class="abs about-sub">We Serve Accross Whole North America</p>
  <p class="abs about-text">Lorem ipsum dolor sit amet, consectetuer adipiscing elit, sed diam nonummy nibh euismod tincidunt ut laoreet dolore magna aliquam erat volutpat. Ut wisi enim ad minim veniam, quis nostrud exerci tation ullamcorper suscipit lobortis nisl aliquip ex ea commodo consequat. Duis autem vel eum iriure dolor in hendrerit ivulputate velit esse molestie consequat, vel illum dolore eu feugiat nulla facilisis</p>
  <div class="abs btn" style="left:531px;top:918px;width:136px;height:46px">Read More</div>
</section>

<div class="abs divider"></div>

<section>
  <h2 class="abs section-title" style="top:1119px"><b>OUR</b> SERVICES FOR</h2>
  <div class="abs title-rule" style="top:1172px;left:560px;width:80px"></div>
  <div class="abs card" style="left:82px">
    <div class="photo"><div role="img" aria-label="Photo of an experienced driver at the wheel of a truck cab" style="background:linear-gradient(135deg,#5f7f8f,#2f3d47)"></div></div>
    <h3>Experienced Drivers</h3>
    <p>Lorem ipsum dolor sit amet, consectetuer adipiscing elit, sed diam nonummy nibh euismod tincidunt ut laoreet dolore magna aliquam erat volutpat.</p>
    <div class="btn">Read More</div>
  </div>
  <div class="abs card" style="left:347px">
    <div class="photo"><div role="img" aria-label="Photo of trainees at a truck driving simulator" style="background:linear-gradient(135deg,#c9c9c4,#4a5460)"></div></div>
    <h3>Inexperienced Drivers</h3>
    <p>Lorem ipsum dolor sit amet, consectetuer adipiscing elit, sed diam nonummy nibh euismod tincidunt ut laoreet dolore magna aliquam erat volutpat.</p>
    <div class="btn">Read More</div>
  </div>
  <div class="abs card" style="left:612px">
    <div class="photo"><div role="img" aria-label="Photo of a smiling driver giving a thumbs up beside a blue truck" style="background:linear-gradient(135deg,#6aa0d0,#2d5e92)"></div></div>
    <h3>CDL Training</h3>
    <p>Lorem ipsum dolor sit amet, consectetuer adipiscing elit, sed diam nonummy nibh euismod tincidunt ut laoreet dolore magna aliquam erat volutpat.</p>
    <div class="btn">Read More</div>
  </div>
  <div class="abs card" style="left:877px">
    <div class="photo"><div role="img" aria-label="Photo of a military veteran driver standing by a truck" style="background:linear-gradient(135deg,#e6e6e6,#27406e)"></div></div>
    <h3>Military Veterans</h3>
    <p>Lorem ipsum dolor sit amet, consectetuer adipiscing elit, sed diam nonummy nibh euismod tincidunt ut laoreet dolore magna aliquam erat volutpat.</p>
    <div class="btn">Read More</div>
  </div>
</section>

<section>
  <div class="abs band"></div>
  <div class="abs band-photo" role="img" aria-label="Photo of a truck driver seated on the step of a black truck"></div>
  <h2 class="abs band-title"><b>Insterested</b> Truck Drivers</h2>
  <p class="abs band-text">Lorem ipsum dolor sit amet, consectetuer adipiscing elit, sed diam nonummy nibh euismod tincidunt ut laoreet dolore volutpat.</p>
  <div class="abs btn apply">APPLY NOW - RHC Driver Application</div>
</section>

<footer>
  <div class="abs footer"></div>
  <h4 class="abs f-head" style="left:82px">Quick Links</h4><div class="abs f-line" style="left:82px"></div>
  <ul class="abs f-links"><li>Home</li><li>About Us</li><li>Services</li><li>Jobs</li><li>Contact Us</li></ul>

  <h4 class="abs f-head" style="left:239px">Contact Details</h4><div class="abs f-line" style="left:239px"></div>
  <div class="abs f-contact" style="top:2142px"><svg width="20" height="26" viewBox="0 0 20 26"><path d="M10 1 A8 8 0 0 1 18 9 Q18 15 10 25 Q2 15 2 9 A8 8 0 0 1 10 1Z" fill="#fff"/><circle cx="10" cy="9" r="3" fill="#8b8b8f"/></svg><span>Street Name, City Name<br>State Zipcode</span></div>
  <div class="abs f-contact" style="top:2225px"><svg width="22" height="22" viewBox="0 0 24 24"><path d="M6 2 L10 7 L8 10 Q10 14 14 16 L17 14 L22 18 L19 22 Q10 22 4 14 Q1 8 6 2Z" fill="#fff"/></svg><span>555.014.2290</span></div>
  <div class="abs f-contact" style="top:2286px"><svg width="24" height="18" viewBox="0 0 30 20"><rect x="1" y="1" width="28" height="18" fill="none" stroke="#fff" stroke-width="2"/><path d="M1 1 L15 12 L29 1" fill="none" stroke="#fff" stroke-width="2"/></svg><span>inquiry@ridgelinehaul.com</span></div>

  <h4 class="abs f-head" style="left:570px">Location Map</h4><div class="abs f-line" style="left:570px"></div>
  <div class="abs map" role="img" aria-label="Map showing the company location"></div>

  <h4 class="abs f-head" style="left:912px">Follow Us On</h4><div class="abs f-line" style="left:912px"></div>
  <div class="abs social-c" style="left:913px" aria-label="Social profile"></div>
  <div class="abs social-c" style="left:957px" aria-label="Social profile"></div>
  <div class="abs social-c" style="left:1002px" aria-label="Social profile"></div>
  <div class="abs btn f-apply">APPLY NOW<br>RHC Driver Application</div>

  <div class="abs bar"></div>
  <p class="abs copy">Copyright © 2019 Ridgeline Haul Carriers. All Rights Reserved.</p>
  <div class="abs social-s" style="left:954px;background:#3b5998" aria-label="Social profile"></div>
  <div class="abs social-s" style="left:997px;background:#38a1d6" aria-label="Social profile"></div>
  <div class="abs social-s" style="left:1040px;background:#16588f" aria-label="Social profile"></div>
  <div class="abs social-s" style="left:1083px;background:#d2323a" aria-label="Social profile"></div>
</footer>
</body>
</html>
```